Marwick Partners Exit Plan business consultant web site

This website is for a consulting business that helps other businesses with exit plans. Essentially, assists them with the sale of their business. This website should be very professional, almost with a wall street look. I would like a very attractive image on the homepage. Perhaps something that denotes success. Perhaps a picture of palm trees and a beach? I will leave it to you for interpretation.

Across the screen I would like the words "Does your business have an exit plan?"

Below that it should read the following:
Let us help you with a completely impartial, no obligation assessment (button with link to the contact page)

Also, please use logo in a prominent place on the website so it's easily seen.

Target Market(s)

Males 40+

Coding

Coded - Design and coding required

Number of Pages Required

5+ page

Colors

Designer to choose colors to be used in the design.

Requirements
Must have
• The tabs for the homepage on the top should be:
• 1. About us
• 2. Services
• 3. Industries
• 4. Our success
• 5. Contact
Nice to have
• Clean, professional image.
• Please put FB, Twitter, Linked In - logos at bottom.
• Here are two examples of a website to give you an idea:
• https://notes.quelvarocapital.example/library/why-every-business-owner-should-have-an-exit-plan
Should not have
• nothing whimsical or cartoon like

```html
<!DOCTYPE html>
<html lang="en">
<head>
<meta charset="utf-8">
<title>Marwick Partners — Exit Planning</title>
<link rel="stylesheet" href="https://fonts.googleapis.com/css2?family=Libre+Baskerville&family=Arimo:wght@400;700&family=Open+Sans:wght@400&display=swap">
<style>
:root{
  --ink:#111;
  --black:#000;
  --white:#fff;
  --hex-gray:#6c6c6e;
  --about-bg:#dcdcdc;
  --muted:#666;
  --footer-text:#333;
}
*{box-sizing:border-box;margin:0;padding:0}
html,body{width:1200px;height:2907px;overflow:hidden;background:var(--white)}
body{position:relative;font-family:'Arimo',Arial,sans-serif;color:var(--ink)}
.abs{position:absolute}
.serif{font-family:'Libre Baskerville',Georgia,serif;font-weight:400}

/* hero */
.hero{left:0;top:0;width:1200px;height:796px;
  background:linear-gradient(100deg,#5a5a5c 0%,#7a7a7c 35%,#6a6a6c 60%,#3e3e40 100%)}
.nav a{position:absolute;top:68px;font-size:14px;color:#e6e6e6;text-decoration:none;letter-spacing:.2px}
.nav a.active{color:var(--white);border-bottom:2px solid var(--white);padding-bottom:3px}
.brand{left:400px;top:22px;width:400px;text-align:center;color:var(--white)}
.brand-mark{width:70px;height:86px;border:2px solid var(--white);margin:0 auto 22px}
.brand-name{font-family:'Libre Baskerville',Georgia,serif;font-size:21px;letter-spacing:1px;white-space:nowrap;line-height:26px}
.hero-title{left:0;top:286px;width:1200px;text-align:center;color:var(--white);font-size:38px;line-height:52px;white-space:nowrap}
.hero-sub{left:0;top:398px;width:1200px;text-align:center;color:var(--white);font-size:21px;white-space:nowrap}
.btn{display:block;text-align:center;text-decoration:none;font-size:17px}
.btn-light{color:var(--white);border:2px solid var(--white)}
.btn-dark{color:var(--ink);border:2px solid #333;font-size:16px}
.arrow{top:338px}

/* about */
.about{left:0;top:796px;width:1200px;height:462px;background:var(--about-bg)}
.about-photo{left:209px;top:829px;width:274px;height:328px;border:4px solid #222;padding:6px;background:#f2f2f2}
.about-photo div{width:100%;height:100%;border:3px solid #222;background:linear-gradient(135deg,#3a3a3a,#8a8a8a 55%,#2a2a2a)}
.about-title{left:563px;top:842px;font-size:35px}
.about-text{left:563px;font-family:'Open Sans',Arial,sans-serif;font-size:15px;line-height:25px;width:510px;color:#222}

/* services */
.section-title{left:0;width:1200px;text-align:center;font-size:35px}
.section-sub{left:0;top:1378px;width:1200px;text-align:center;font-size:19px;color:var(--muted)}
.hex{top:1443px;width:296px;height:370px;color:var(--white);text-align:center;
  clip-path:polygon(50% 0,100% 22%,100% 78%,50% 100%,0 78%,0 22%)}
.hex.dark{background:var(--black)}
.hex.gray{background:var(--hex-gray)}
.hex .icon{position:absolute;left:99px;top:52px;width:99px;height:99px;border-radius:50%}
.hex.dark .icon{background:var(--hex-gray)}
.hex.gray .icon{background:var(--black)}
.hex h3{position:absolute;left:0;top:170px;width:100%;font-size:20px;font-weight:700}
.hex p{position:absolute;left:24px;top:206px;width:248px;font-family:'Open Sans',Arial,sans-serif;font-size:13px;line-height:18px;color:#ddd}
.hex .more{position:absolute;left:129px;top:290px}

/* industries */
.card{top:1951px;width:321px;height:217px;color:var(--white)}
.card .photo{width:100%;height:100%}
.card span{position:absolute;left:0;bottom:22px;width:100%;text-align:center;font-weight:700;font-size:16px}
.dots{left:556px;top:2198px}

/* success */
.success{left:0;top:2280px;width:1200px;height:486px;
  background:linear-gradient(180deg,#4e5a6e 0%,#6d7688 45%,#5a5a66 75%,#3a3e4c 100%)}
.success-text{left:240px;width:720px;text-align:center;color:#eee;font-size:17px;line-height:25px}

/* footer */
.footer-nav a{position:absolute;top:2806px;font-size:13px;color:var(--footer-text);text-decoration:none}
.copy{left:165px;top:2838px;font-size:11px;color:#555}
.social{top:2800px;width:34px;height:34px;border:2px solid #222;border-radius:50%}
</style>
</head>
<body>

<!-- hero -->
<section class="hero abs" role="img" aria-label="Photo of a businesswoman holding a tablet over a city skyline with market figures"></section>
<nav class="nav">
  <a href="#" class="active" style="left:187px">HOME</a>
  <a href="#" style="left:267px">ABOUT US</a>
  <a href="#" style="left:376px">SERVICES</a>
  <a href="#" style="left:714px">INDUSTRIES</a>
  <a href="#" style="left:836px">OUR SUCCESS</a>
  <a href="#" style="left:975px">CONTACT</a>
</nav>
<div class="brand abs">
  <div class="brand-mark"></div>
  <div class="brand-name">MARWICK PARTNERS</div>
</div>
<svg class="arrow abs" style="left:58px" width="26" height="42" viewBox="0 0 26 42"><path d="M22 3 5 21l17 18" fill="none" stroke="#fff" stroke-width="5"/></svg>
<svg class="arrow abs" style="left:1122px" width="26" height="42" viewBox="0 0 26 42"><path d="M4 3l17 18L4 39" fill="none" stroke="#fff" stroke-width="5"/></svg>
<h1 class="hero-title abs serif">DOES YOUR BUSINESS HAVE<br>AN EXIT PLAN?</h1>
<p class="hero-sub abs">Let us help you with a completely impartial, no obligation assessment</p>
<a href="#" class="btn btn-light abs" style="left:511px;top:449px;width:190px;height:53px;line-height:49px">CONTACT US</a>
<svg class="abs" style="left:0;top:676px" width="1200" height="122" viewBox="0 0 1200 122">
  <polygon points="0,104 606,6 1200,100 1200,122 0,122" fill="#fff"/>
  <polygon points="606,14 1200,108 1200,115 606,22" fill="#8c8c8c"/>
  <polygon points="0,122 606,20 1200,120 1200,122" fill="#dcdcdc"/>
</svg>

<!-- about -->
<section class="about abs"></section>
<div class="about-photo abs"><div role="img" aria-label="Photo of a team meeting around a conference table"></div></div>
<h2 class="about-title abs serif">ABOUT US</h2>
<p class="about-text abs" style="top:900px">Etiam eleifend metus vitae adipiscing semper mauris ipsum iaculis elit congue gravida elit mi egestas orci Curabitur pede</p>
<p class="about-text abs" style="top:977px">Maecenas aliquet velit vel turpis Mauris neque metus malesuada nec ultricies sit amet porttitor mattis enim In massa libero interdum nec interdum vel blandit sed nulla In ullamcorper est eget tempor cursuClass aptent taciti sociosqu ad litora torquent per conubia</p>
<a href="#" class="btn btn-dark abs" style="left:568px;top:1102px;width:173px;height:48px;line-height:44px">LEARN MORE</a>

<!-- services -->
<h2 class="section-title abs serif" style="top:1328px">SERVICES</h2>
<p class="section-sub abs">Praesent sit amet est In dictum dolor eu dictum porttitor enim</p>

<article class="hex dark abs" style="left:0">
  <div class="icon"></div><h3>SERVICE TITLE</h3>
  <p>Praesent sit amet est In dictum dolor eu dictum porttitor enim felis viverra mi eget luctus massa</p>
  <svg class="more" width="38" height="38" viewBox="0 0 38 38"><circle cx="19" cy="19" r="19" fill="#fff"/><path d="M12 16l7 7 7-7" fill="none" stroke="#000" stroke-width="3"/></svg>
</article>
<article class="hex gray abs" style="left:304px">
  <div class="icon"></div><h3>STRATEGY</h3>
  <p>Praesent sit amet est In dictum dolor eu dictum porttitor enim felis viverra mi eget luctus massa</p>
  <svg class="more" width="38" height="38" viewBox="0 0 38 38"><circle cx="19" cy="19" r="19" fill="#fff"/><path d="M12 16l7 7 7-7" fill="none" stroke="#6c6c6e" stroke-width="3"/></svg>
</article>
<article class="hex dark abs" style="left:606px">
  <div class="icon"></div><h3>CONSULTING</h3>
  <p>Praesent sit amet est In dictum dolor eu dictum porttitor enim felis viverra mi eget luctus massa</p>
  <svg class="more" width="38" height="38" viewBox="0 0 38 38"><circle cx="19" cy="19" r="19" fill="#fff"/><path d="M12 16l7 7 7-7" fill="none" stroke="#000" stroke-width="3"/></svg>
</article>
<article class="hex gray abs" style="left:909px;width:291px">
  <div class="icon"></div><h3>GROWTH SALES</h3>
  <p>Praesent sit amet est In dictum dolor eu dictum porttitor enim felis viverra mi eget luctus massa</p>
  <svg class="more" width="38" height="38" viewBox="0 0 38 38"><circle cx="19" cy="19" r="19" fill="#fff"/><path d="M12 16l7 7 7-7" fill="none" stroke="#6c6c6e" stroke-width="3"/></svg>
</article>

<!-- industries -->
<h2 class="section-title abs serif" style="top:1878px;font-size:31px">INDUSTRIES</h2>
<div class="card abs" style="left:100px"><div class="photo" role="img" aria-label="Photo of colleagues talking at an office table" style="background:linear-gradient(180deg,#5a5450,#3c3a3a)"></div><span>INDUSTRY TITLE HERE</span></div>
<div class="card abs" style="left:431px"><div class="photo" role="img" aria-label="Photo of a team discussion in a modern office" style="background:linear-gradient(180deg,#55606a,#2e363e)"></div><span style="bottom:30px">INDUSTRY TITLE HERE</span></div>
<div class="card abs" style="left:762px"><div class="photo" role="img" aria-label="Photo of coworkers smiling in a brick-walled workspace" style="background:linear-gradient(180deg,#7a6050,#5a4a40)"></div><span>INDUSTRY TITLE HERE</span></div>
<svg class="dots abs" width="88" height="20" viewBox="0 0 88 20">
  <circle cx="10" cy="10" r="9" fill="#000"/><path d="M12 6l-4 4 4 4" fill="none" stroke="#fff" stroke-width="1.5"/>
  <circle cx="30" cy="10" r="4.5" fill="#000"/><circle cx="44" cy="10" r="4.5" fill="#999"/><circle cx="58" cy="10" r="4.5" fill="#999"/>
  <circle cx="78" cy="10" r="9" fill="#000"/><path d="M76 6l4 4-4 4" fill="none" stroke="#fff" stroke-width="1.5"/>
</svg>

<!-- success -->
<section class="success abs" role="img" aria-label="Photo of a businessman looking out over a city skyline at sunrise"></section>
<h2 class="section-title abs serif" style="top:2376px;color:#fff">OUR SUCCESS</h2>
<p class="success-text abs" style="top:2437px">Praesent elementum elit at tellus Curabitur metus ipsum luctus eu malesuada ut tincidunt sed diam vdisse risus nibh ultricies eu volutpat non condimentum hendrerit augue</p>
<p class="success-text abs" style="top:2513px">Etiam eleifend metus vitae adipiscing semper mauris ipsum iaculis elit congue gravida elit mi egestas orci Curabitur pedeMaecenas aliquet velit vel turpis Mauris neque metus malesuada nec ultricies sit amet porttitor mattis enim In massa libero</p>
<a href="#" class="btn btn-light abs" style="left:515px;top:2619px;width:173px;height:49px;line-height:45px;font-size:16px">LEARN MORE</a>

<!-- footer -->
<nav class="footer-nav">
  <a href="#" style="left:165px">HOME</a>
  <a href="#" style="left:225px">ABOUT US</a>
  <a href="#" style="left:311px">SERVICES</a>
  <a href="#" style="left:394px">INDUSTRIES</a>
  <a href="#" style="left:489px">OUR SUCCESS</a>
  <a href="#" style="left:601px">CONTACT</a>
</nav>
<p class="copy abs">© 2020 Company Name &nbsp;All right reserved</p>
<a href="#" class="social abs" style="left:955px" aria-label="Social profile one"></a>
<a href="#" class="social abs" style="left:993px" aria-label="Social profile two"></a>
<a href="#" class="social abs" style="left:1031px" aria-label="Social profile three"></a>

</body>
</html>
```